Business Card Design Project

We have recently completed CraftHive projects for a new logo and wesbite.
We now require new business cards.
We hand out very little printed material to clients as all information is online. When we do hand out something, like a business card, we want it to have real impact and make a statement about the quality and professionalism of our company.
We have an idea of what we want our card to look like but we want a designer to make sure they have impact and look great.
Our requirements are…
Size: 85mm X 55mm - Landscape
Front of card: Logo plus the following contact information.
Dennis Marlow
Operations Manager
Phone +44(0) 1632 xxx xxx
Mobile +44(0) 7700 xxx xxx
Email denmo@korvantix.example
Address 17 Pellick Row, Aberdeen AB12 9QZ
Website www.korvantix.example
How you layout the front of the card is up to you, we would like to see some different ideas. Attached are two versions of our logo that may be used.
Back of card: We would like this to be simple but again have impact. Our current thought is to have the logo or just the large W design from the logo in white against a dark background, perhaps made up from the dark green in the logo.
The logos are attached so you can see the colours in them but the dark ones are..
Dark Blue = C:88, M:55, Y:44, K:28
Dark Green = C:87, M:53, Y:50, K:50
We sometimes also use a bright orange as an accent or highlight colour…
Orange: = C:0, M:39, Y:94, K:0

```html
<!DOCTYPE html>
<html lang="en">
<head>
<meta charset="utf-8">
<title>Korvantix Business Card Concepts</title>
<link rel="stylesheet" href="https://fonts.googleapis.com/css2?family=Source+Sans+3:ital,wght@0,400;0,600;0,700;0,800;1,700&display=swap">
<style>
  :root {
    --stage: #e8e5e1;
    --card: #ffffff;
    --ink: #2b2b2b;
    --label: #222222;
    --brand-dark: #1c4952;
    --brand-deep: #143f47;
    --brand-mid: #3e6f7a;
    --brand-light: #7ba9ae;
    --brand-faint: #4d7f88;
    --band-start: #2e5e6a;
    --band-end: #7eabb0;
    --url: #2c4853;
  }
  * { margin: 0; padding: 0; box-sizing: border-box; }
  html, body { width: 1200px; height: 788px; overflow: hidden; }
  body {
    position: relative;
    background: var(--stage);
    font-family: "Source Sans 3", "Myriad Pro", sans-serif;
    color: var(--ink);
  }
  .view-label {
    position: absolute;
    width: 502px;
    text-align: center;
    font-size: 22px;
    font-weight: 400;
    color: var(--label);
  }
  .card {
    position: absolute;
    width: 502px;
    height: 325px;
    border-radius: 18px;
    background: var(--card);
    overflow: hidden;
    box-shadow: 0 4px 12px rgba(0,0,0,0.25);
  }
  .card--dark { background: var(--brand-deep); }

  /* Front */
  .front-band {
    position: absolute; left: 0; top: 0; width: 502px; height: 96px;
    background: linear-gradient(90deg, var(--band-start), var(--band-end));
  }
  .holder { position: absolute; right: 24px; top: 24px; text-align: right; color: #fff; }
  .holder__name { font-size: 18px; font-weight: 700; line-height: 1.1; }
  .holder__role { font-size: 13.5px; font-weight: 400; opacity: 0.95; }
  .brand-lockup {
    position: absolute;
    display: flex; align-items: center; gap: 10px;
  }
  .brand-lockup__dot { border-radius: 50%; background: var(--brand-mid); flex: none; }
  .brand-name {
    font-weight: 800;
    color: var(--brand-dark);
    letter-spacing: 0.5px;
    line-height: 1;
  }
  .front-brand { left: 36px; top: 194px; }
  .front-brand .brand-lockup__dot { width: 22px; height: 22px; }
  .front-brand .brand-name { font-size: 32px; }
  .address { position: absolute; left: 36px; top: 264px; font-size: 14px; line-height: 20px; color: var(--ink); }
  .contacts { position: absolute; right: 24px; top: 202px; list-style: none; text-align: right; font-size: 14px; line-height: 23.5px; color: var(--ink); }
  .contacts b { font-style: italic; font-weight: 700; }

  /* Backs */
  .back-brand { left: 0; right: 0; justify-content: center; }
  .back-one .back-brand { top: 108px; }
  .back-one .brand-lockup__dot { width: 34px; height: 34px; }
  .back-one .brand-name { font-size: 48px; }
  .back-three .back-brand { top: 150px; }
  .back-three .brand-lockup__dot { width: 40px; height: 40px; }
  .back-three .brand-name { font-size: 56px; }
  .web {
    position: absolute; left: 0; right: 0; text-align: center;
    font-size: 18px; letter-spacing: 2.6px; color: var(--url);
  }
  .back-one .web { top: 286px; }
  .back-three .web { top: 280px; }
  .back-two .back-brand { top: 128px; }
  .back-two .brand-lockup__dot { width: 50px; height: 50px; background: var(--brand-faint); }
  .back-two .brand-name { font-size: 62px; color: var(--brand-faint); }
</style>
</head>
<body>
  <div class="view-label" style="left:65px; top:18px;">Front</div>
  <div class="view-label" style="left:625px; top:18px;">Back - 1</div>
  <div class="view-label" style="left:65px; top:402px;">Back - 2</div>
  <div class="view-label" style="left:625px; top:402px;">Back - 3</div>

  <section class="card card-front" style="left:65px; top:52px;">
    <div class="front-band" role="img" aria-label="Decorative teal header band"></div>
    <div class="holder">
      <p class="holder__name">Dennis Marlow</p>
      <p class="holder__role">Operations Manager</p>
    </div>
    <div class="brand-lockup front-brand">
      <span class="brand-lockup__dot"></span>
      <span class="brand-name">KORVANTIX</span>
    </div>
    <p class="address">17 Pellick Row<br>Aberdeen AB12 9QZ</p>
    <ul class="contacts">
      <li><b>c</b> : +44(0) 7700 xxx xxx</li>
      <li><b>p</b> : +44(0) 1632 xxx xxx</li>
      <li><b>e</b> : denmo@korvantix.example</li>
      <li><b>w</b> : www.korvantix.example</li>
    </ul>
  </section>

  <section class="card back-one" style="left:625px; top:53px;">
    <div class="brand-lockup back-brand">
      <span class="brand-lockup__dot"></span>
      <span class="brand-name">KORVANTIX</span>
    </div>
    <p class="web">www.korvantix.example</p>
  </section>

  <section class="card card--dark back-two" style="left:65px; top:443px;">
    <div class="brand-lockup back-brand">
      <span class="brand-lockup__dot"></span>
      <span class="brand-name">KORVANTIX</span>
    </div>
  </section>

  <section class="card back-three" style="left:625px; top:443px;">
    <div class="brand-lockup back-brand">
      <span class="brand-lockup__dot"></span>
      <span class="brand-name">KORVANTIX</span>
    </div>
    <p class="web">www.korvantix.example</p>
  </section>
</body>
</html>
```